Distribution/Printing company needs a web site to inform prospective customers on what we do.

Distribution/Printing/Packaging company needs a web site to inform prospective customers on what we do. Please look at our direct to consumer web site (under development) for an idea of the product lines we sell: storedev.maplewickhaven.com
Logo files are attached as is a flyer that is under development which contains other information about the company (this is to be used for content- not to be posted as is). The web site should be focused on our business customer base and is not intended to be direct to consumer. Site should have a link to our consumer web site.
Site design should be mobile friendly, or mobile could be redirected to a mobile version. This web site will be strictly informational and will not be designed for any sales transactions.

Target Market(s)

Manufacturing and retail businesses, any other multi-site business that would benefit from centralized pricing and budget controls we can provide (banks, medical/dental offices, educational facilities, etc).

Industry/Entity Type

It Company

Coding

Coded - Design and coding required

Number of Pages Required

5+ page

Requirements
Must have
• 1) Top level menu: Products, about us, locations, contact us, news
• 2) page with news/promotions that is easily updated
• 3) "contact us" form (name, company, phone, email address) email link
• 4) link to www.store.maplewickhaven.com with information that lower pricing is available for businesses
• 5) SEO keywords
• 6) Link to powerpoint presentation file
Nice to have
• 1) our phone number should appear on every page near the top

```html
<!DOCTYPE html>
<html lang="en">
<head>
<meta charset="utf-8">
<title>Maplewick Haven Supply – Distribution, Printing &amp; Packaging</title>
<link rel="stylesheet" href="https://fonts.googleapis.com/css2?family=Open+Sans:wght@400;600;700&family=Crimson+Text:wght@400&display=swap">
<style>
:root{
  --teal:#17a99a;
  --header:#333333;
  --footer:#4a4a4a;
  --ink:#333333;
  --muted:#6a6a6a;
  --section-grey:#f3f3f3;
  --card-border:#e6e6e6;
  --btn-grey:#777777;
  --white:#ffffff;
}
*{box-sizing:border-box;margin:0;padding:0}
html,body{width:715px;height:1200px;overflow:hidden}
body{font-family:"Open Sans",Arial,sans-serif;color:var(--ink);background:var(--white);position:relative}

/* Header */
.site-header{height:92px;background:var(--header);position:relative}
.brand{position:absolute;left:78px;top:54px;color:var(--white)}
.brand-name{font-size:9.5px;font-weight:700;letter-spacing:.2px;display:block}
.brand-tagline{font-size:6.5px;font-weight:600;display:block;margin-top:2px;padding-left:5px}
.search{position:absolute;left:516px;top:27px;width:118px;height:20px;background:var(--white);border:1px solid #ccc;display:flex;align-items:center;justify-content:space-between;padding:0 7px}
.search span{font-size:7px;color:#aaa;font-style:italic}
.main-nav{position:absolute;right:78px;top:60px;display:flex;gap:0}
.main-nav a{color:var(--white);text-decoration:none;font-size:7.5px;font-weight:600;padding:4px 8px;margin-left:8px;letter-spacing:.2px}
.main-nav a.is-active{border:1.5px solid var(--teal);color:var(--teal)}

/* Hero */
.hero{position:relative;height:338px;overflow:hidden}
.hero-photo{position:absolute;inset:0;background:radial-gradient(ellipse at 60% 45%,#f2f1ee 0%,#dedbd6 60%,#c9c5bf 100%)}
.hero-photo .boxes{position:absolute;left:330px;top:0;width:350px;height:338px;background:linear-gradient(160deg,#b08f68 0%,#a38260 45%,#6b7f9c 80%,#4e6587 100%);opacity:.85;border-radius:4px}
.hero-content{position:absolute;left:78px;top:68px;width:290px}
.hero-title{font-family:"Crimson Text",Georgia,serif;font-weight:400;font-size:27px;line-height:32px;color:#2c2c2c;letter-spacing:.5px}
.hero-text{margin-top:20px;font-size:8px;line-height:16.5px;color:#444}
.hero-controls{position:absolute;left:78px;top:212px;display:flex;gap:2px}
.hero-controls span{width:29px;height:29px;border-radius:50%;background:#9a9a9a;display:flex;align-items:center;justify-content:center}

/* Welcome */
.welcome{height:180px;text-align:center;padding-top:40px}
.section-title{font-size:18.5px;font-weight:400;color:#222}
.section-title em{font-style:normal;color:var(--teal)}
.welcome p{width:540px;margin:12px auto 0;font-size:7.4px;line-height:16px;color:#555}
.btn-primary{display:inline-block;margin-top:15px;background:var(--teal);color:var(--white);font-size:7.5px;font-weight:600;padding:7px 17px;text-decoration:none}

/* Products */
.products{height:507px;background:var(--section-grey);padding-top:30px;text-align:center}
.product-grid{display:grid;grid-template-columns:repeat(4,131px);gap:16px 12px;width:560px;margin:12px auto 0}
.product-card{height:188px;background:var(--white);border:1px solid var(--card-border);padding:9px 9px 0;text-align:center}
.product-image{height:88px}
.product-name{margin-top:12px;font-size:11px;font-weight:600;color:var(--teal)}
.product-desc{margin-top:6px;font-size:7.2px;line-height:12px;color:#666}
.btn-detail{display:inline-block;margin-top:11px;background:var(--btn-grey);color:var(--white);font-size:7px;font-weight:600;padding:4px 8px;text-decoration:none}
.product-card.is-featured{background:var(--teal);border-color:var(--teal)}
.product-card.is-featured .product-image{background-color:var(--white)}
.product-card.is-featured .product-name,
.product-card.is-featured .product-desc{color:var(--white)}
.product-card.is-featured .product-desc{font-size:7.2px}
.product-card.is-featured .btn-detail{background:#2fc0b0}

/* Footer */
.site-footer{height:83px;background:var(--footer);position:relative;color:#ddd}
.footer-links{position:absolute;left:80px;top:20px;font-size:7.2px}
.footer-links a{color:#eee;text-decoration:none}
.footer-links .sep{margin:0 4px}
.copyright{position:absolute;left:80px;top:38px;font-size:6.5px;color:#aaa}
.payments{position:absolute;left:299px;top:19px}
.payments h4,.social h4{font-weight:400;font-size:7px;letter-spacing:.3px;color:#eee}
.payment-list{display:flex;gap:3px;margin-top:12px;padding-left:11px}
.payment-list span{width:23px;height:15px;border-radius:2px;background:#d9d9d9}
.social{position:absolute;left:509px;top:19px}
.social h4{font-size:8.5px}
.social-list{display:flex;gap:4px;margin-top:10px}
.social-list span{width:20px;height:20px;border-radius:50%;background:#9a9a9a}
</style>
</head>
<body>

<header class="site-header">
  <a class="brand" href="#">
    <span class="brand-name">MAPLEWICK HAVEN SUPPLY</span>
    <span class="brand-tagline">Packaging • Printing • Distribution</span>
  </a>
  <div class="search">
    <span>Search</span>
    <svg width="8" height="8" viewBox="0 0 10 10"><circle cx="4" cy="4" r="3" fill="none" stroke="#333" stroke-width="1.5"/><line x1="6.3" y1="6.3" x2="9" y2="9" stroke="#333" stroke-width="1.6"/></svg>
  </div>
  <nav class="main-nav">
    <a href="#" class="is-active">HOME</a>
    <a href="#">ABOUT</a>
    <a href="#">SERVICES</a>
    <a href="#">BLOG</a>
    <a href="#">CONTACT</a>
  </nav>
</header>

<section class="hero">
  <div class="hero-photo" role="img" aria-label="Photo of a person in jeans and a plaid shirt carrying a stack of cardboard shipping boxes, with a fragile-labelled box falling beside them">
    <div class="boxes"></div>
  </div>
  <div class="hero-content">
    <h1 class="hero-title">Distribution/Printing/<br>Packaging company</h1>
    <p class="hero-text">Neque porro quisquam est, qui dolorem ipsum quia dolor sit amet, consectetur, adipisci velit, sed quia non numquam eius modi tempora incidunt ut labore et dolore magnam aliquam</p>
  </div>
  <div class="hero-controls">
    <span><svg width="8" height="10" viewBox="0 0 8 10"><polyline points="6,1 2,5 6,9" fill="none" stroke="#fff" stroke-width="1"/></svg></span>
    <span><svg width="8" height="10" viewBox="0 0 8 10"><polyline points="2,1 6,5 2,9" fill="none" stroke="#fff" stroke-width="1"/></svg></span>
  </div>
</section>

<section class="welcome">
  <h2 class="section-title">Welcome to Our Site</h2>
  <p>Sed ut perspiciatis unde omnis iste natus error sit voluptatem accusantium doloremque laudantium, totam rem aperiam, eaque ipsa quae ab illo inventore veritatis et quasi architecto beatae vitae dicta sunt explicabo. Nemo enim ipsam voluptatem quia voluptas sit aspernatur aut odit aut fugit, sed quia consequuntur magni dolores eos qui ratione voluptatem sequi nesciunt.</p>
  <a class="btn-primary" href="#">READ MORE</a>
</section>

<section class="products">
  <h2 class="section-title">Featured <em>Products</em></h2>
  <div class="product-grid">
    <article class="product-card is-featured">
      <div class="product-image" role="img" aria-label="Stacked plastic storage bins in red, yellow and blue" style="background:linear-gradient(135deg,#fff 0%,#f4d9d6 30%,#f7ecb2 55%,#cdd9f0 80%,#fff 100%)"></div>
      <h3 class="product-name">Product Name</h3>
      <p class="product-desc">Neque porro quisquam est qui dolorem ipsum quia dolor.</p>
      <a class="btn-detail" href="#">View Detail</a>
    </article>
    <article class="product-card">
      <div class="product-image" role="img" aria-label="Open cardboard shipping boxes" style="background:radial-gradient(ellipse at center,#d2b38a 0%,#e9dcc8 55%,#fff 80%)"></div>
      <h3 class="product-name">Product Name</h3>
      <p class="product-desc">Neque porro quisquam est qui dolorem ipsum quia dolor.</p>
      <a class="btn-detail" href="#">View Detail</a>
    </article>
    <article class="product-card">
      <div class="product-image" role="img" aria-label="Office supplies: calculator, pen holder and stapler" style="background:radial-gradient(ellipse at center,#9a9a9a 0%,#d9c9c9 50%,#fff 80%)"></div>
      <h3 class="product-name">Product Name</h3>
      <p class="product-desc">Neque porro quisquam est qui dolorem ipsum quia dolor.</p>
      <a class="btn-detail" href="#">View Detail</a>
    </article>
    <article class="product-card">
      <div class="product-image" role="img" aria-label="Assorted light bulbs" style="background:radial-gradient(ellipse at center,#d8dde2 0%,#eef0f2 50%,#fff 80%)"></div>
      <h3 class="product-name">Product Name</h3>
      <p class="product-desc">Neque porro quisquam est qui dolorem ipsum quia dolor.</p>
      <a class="btn-detail" href="#">View Detail</a>
    </article>
    <article class="product-card">
      <div class="product-image" role="img" aria-label="Emergency safety kit with red backpack and supplies" style="background:radial-gradient(ellipse at center,#d8463d 0%,#eab6a8 50%,#fff 80%)"></div>
      <h3 class="product-name">Product Name</h3>
      <p class="product-desc">Neque porro quisquam est qui dolorem ipsum quia dolor.</p>
      <a class="btn-detail" href="#">View Detail</a>
    </article>
    <article class="product-card">
      <div class="product-image" role="img" aria-label="Yellow broom" style="background:radial-gradient(ellipse at center,#d5d36a 0%,#eeecc4 45%,#fff 75%)"></div>
      <h3 class="product-name">Product Name</h3>
      <p class="product-desc">Neque porro quisquam est qui dolorem ipsum quia dolor.</p>
      <a class="btn-detail" href="#">View Detail</a>
    </article>
    <article class="product-card">
      <div class="product-image" role="img" aria-label="Cleaning and janitorial supplies" style="background:radial-gradient(ellipse at center,#6b86b5 0%,#d3d6e2 50%,#fff 80%)"></div>
      <h3 class="product-name">Product Name</h3>
      <p class="product-desc">Neque porro quisquam est qui dolorem ipsum quia dolor.</p>
      <a class="btn-detail" href="#">View Detail</a>
    </article>
    <article class="product-card">
      <div class="product-image" role="img" aria-label="Carton of copy paper" style="background:radial-gradient(ellipse at center,#8fa4c8 0%,#e1e6ef 50%,#fff 80%)"></div>
      <h3 class="product-name">Product Name</h3>
      <p class="product-desc">Neque porro quisquam est qui dolorem ipsum quia dolor.</p>
      <a class="btn-detail" href="#">View Detail</a>
    </article>
  </div>
</section>

<footer class="site-footer">
  <nav class="footer-links">
    <a href="#">Search</a><span class="sep">/</span><a href="#">About Us</a><span class="sep">/</span><a href="#">Gallery</a><span class="sep">/</span><a href="#">Sitemap</a>
  </nav>
  <p class="copyright">© 2014 Yoursite. All Rights Reserved.</p>
  <div class="payments">
    <h4>PAYMENT METHODS WE ACCEPT</h4>
    <div class="payment-list"><span></span><span></span><span></span><span></span></div>
  </div>
  <div class="social">
    <h4>Follow Us</h4>
    <div class="social-list"><span></span><span></span><span></span><span></span></div>
  </div>
</footer>

</body>
</html>
```